Velvet Glow Co. Derma Roller packaging design

I need a box designed for a skin care brand called Velvet Glow Co. The box will be for our Derma Roller- a skin rejuvenation device. It will be sold online with lots of competition. I would like a modern, high end design, something that stands out and looks amazing. My logo is blush pink and black, for packaging i need no more than 3 colours, maybe gold if any other colour is used. A photo of a sample derma roller is attached below for an idea of what the product looks like, however my roller with have a clear handle with a black roller. The roller comes in a clear case, the box dimensions will need to be 16 cm long, 4 cm high, 4.5 cm wide.
ATTACHED ARE 2 SAMPLE BOXES AS AN EXAMPLE OF THE SIZE OF BOX REQUIRED!

Target Market(s)

25-50 year old women in the US

Colors
e667a6
000000
efefef

Requirements
Must have
• LOGO
• NAME OF PRODUCT- Cosmetic Derma Roller
• NEEDLE DEPTH- 0.25mm
• CAUTION- For personal use only, Do not use if allergic to metal, Do not use on open skin, wounds or active acne, sterilise roller before and after use.
Nice to have
• BENEFITS- Skin Rejuvenation, Collagen Induction Therapy, Increase product absorption, reduce acne scars and pigmentation
• FEATURES- 540 high quality titanium needles, ultra sharp needle tips, cross-line needle arrangement, ergonomic handle, anti slip grip,

```html
<!DOCTYPE html>
<html lang="en">
<head>
<meta charset="utf-8">
<title>Velvet Glow Co. – Cosmetic Derma Roller Box Sleeve</title>
<link href="https://fonts.googleapis.com/css2?family=Oswald:wght@300;400;500&display=swap" rel="stylesheet">
<style>
  :root {
    --page-bg: #fbf8f7;
    --blush-light: #f3c9cc;
    --blush-mid: #c9979d;
    --mauve-dark: #7e4f5a;
    --label-white: #ffffff;
    --ink: #1d1618;
    --rose-gold-1: #f0c3b4;
    --rose-gold-2: #d9a08e;
    --rose-gold-3: #c58a78;
  }
  * { margin: 0; padding: 0; box-sizing: border-box; }
  html, body { width: 1200px; height: 1200px; overflow: hidden; }
  body {
    background: var(--page-bg);
    font-family: "Oswald", sans-serif;
    position: relative;
  }
  .sleeve {
    position: absolute;
    left: 48px;
    width: 1104px;
    height: 356px;
    box-shadow: 0 3px 10px rgba(90, 50, 60, 0.25);
    overflow: hidden;
  }
  .sleeve--front { top: 182px; }
  .sleeve--back { top: 662px; }

  .facet-pattern { position: absolute; inset: 0; }
  .sleeve--front .facet-pattern {
    background:
      radial-gradient(ellipse 45% 60% at 15% 95%, var(--mauve-dark), transparent 70%),
      radial-gradient(ellipse 35% 55% at 75% 40%, rgba(126, 79, 90, 0.75), transparent 70%),
      radial-gradient(ellipse 40% 45% at 95% 90%, var(--blush-light), transparent 70%),
      linear-gradient(160deg, var(--blush-light) 0%, var(--blush-mid) 55%, var(--mauve-dark) 100%);
  }
  .sleeve--back .facet-pattern {
    background:
      radial-gradient(ellipse 40% 55% at 12% 15%, var(--mauve-dark), transparent 70%),
      radial-gradient(ellipse 35% 60% at 90% 65%, rgba(126, 79, 90, 0.7), transparent 70%),
      radial-gradient(ellipse 40% 45% at 85% 10%, var(--blush-light), transparent 70%),
      linear-gradient(20deg, var(--blush-light) 0%, var(--blush-mid) 55%, var(--mauve-dark) 100%);
  }

  .label {
    position: absolute;
    background: var(--label-white);
  }
  .label--front {
    left: 386px; top: 39px;
    width: 332px; height: 281px;
    border: 3px solid var(--rose-gold-2);
    box-shadow: inset 0 0 0 1px var(--rose-gold-1);
  }
  .label--back {
    left: 248px; top: 58px;
    width: 608px; height: 238px;
  }

  .brand-name {
    position: absolute;
    left: 0; right: 0; top: 92px;
    text-align: center;
    font-weight: 300;
    font-size: 34px;
    letter-spacing: 3px;
    text-transform: uppercase;
    color: var(--ink);
  }
  .product-title {
    position: absolute;
    left: 0; right: 0;
    text-align: center;
    font-size: 30px;
    letter-spacing: 0.5px;
    background: linear-gradient(90deg, var(--rose-gold-1), var(--rose-gold-3) 50%, var(--rose-gold-1) 75%, var(--rose-gold-3));
    -webkit-background-clip: text;
    background-clip: text;
    color: transparent;
  }
  .label--front .product-title { top: 220px; }
  .label--back .product-title { top: 22px; }
  .product-title .light { font-weight: 300; }
  .product-title .bold { font-weight: 500; }

  .info {
    position: absolute;
    left: 29px; right: 24px; top: 76px;
    font-weight: 400;
    font-size: 14.2px;
    line-height: 18px;
    text-transform: uppercase;
    color: var(--ink);
  }
  .info p + p { margin-top: 18px; }
</style>
</head>
<body>
  <section class="sleeve sleeve--front">
    <div class="facet-pattern" role="img" aria-label="Faceted low-poly pattern in blush pink and dusky mauve"></div>
    <div class="label label--front">
      <div class="brand-name">Velvet Glow Co.</div>
      <h1 class="product-title"><span class="light">COSMETIC DERMA</span> <span class="bold">ROLLER</span></h1>
    </div>
  </section>

  <section class="sleeve sleeve--back">
    <div class="facet-pattern" role="img" aria-label="Faceted low-poly pattern in blush pink and dusky mauve"></div>
    <div class="label label--back">
      <h2 class="product-title"><span class="light">COSMETIC DERMA</span> <span class="bold">ROLLER</span></h2>
      <div class="info">
        <p>Benefits: Skin rejuvenation, collagen induction therapy, increase product absorption, reduce acne scars and pigmentation</p>
        <p>Features: 540 high quality 0.25 mm titanium needles, ultra sharp needle tips, cross-line needle arrangement, ergonomic handle, anti slip grip</p>
        <p>Caution: For personal use only, do not use if allergic to metal, do not use on open skin, wounds or active acne, sterilise roller before and after use.</p>
      </div>
    </div>
  </section>
</body>
</html>
```